Meridian Tidewren Pale Ale Beer Label/Badge

We need a Beer Label designed for our first official beer to be launched under The meridian Brand!!
It will be a Pale Ale Called "Tidewren Pale Ale"!

The Meridian has the largest Craft Beer & Cider selection in the Geelong & Surf Coast region. With a funky location and a relaxed vibe, Meridian prides itself on serving delicious, unique seasonal food paired with Australia's best Craft Beer. The meridian is the perfect setting for a relaxed afternoon or evening with friends and can package an experience for larger groups or corporate bookings.

The Meridian Tavern brand has been growing for over a year and a half and the first label needs to integrate The meridian Logo but at the same time bring a fresh, new and eye catching feel to it along with embracing the "Odysseus" story in which we will be naming future beers.

The story of Tidewren is found via the following link
http://lorevault.example/wiki/Tidewren_(folklore)

We expect designers to research The meridian Tavern brand along with the all important Craft Beer Market and demographics. This will, potentially, be the start of many more labels to come for the winning designer!!

Requirements
Must have
• The original "O" needs to be integrated into the new logo and as much as the Greek mythology is being used it needs to be certain that this is an original Australian Craft Beer in the modern age!!
strong, modern & unique!!
Nice to have
• Logo could have a depiction of Tidewren
Should not have
• tackiness or cheap!!

```html
<!DOCTYPE html>
<html lang="en">
<head>
<meta charset="utf-8">
<title>Tidewren Pale Ale – Meridian Tavern + Brewery</title>
<link rel="stylesheet" href="https://fonts.googleapis.com/css2?family=Cinzel:wght@700&family=Jost:wght@500;600&display=swap">
<style>
  :root {
    --backdrop: #e2e2e2;
    --label-white: #ffffff;
    --label-dark: #1f2226;
    --ink: #23262b;
    --helmet-grey: #b9bfcf;
    --pale-cream: #e8e2c4;
    --ale-amber: #b8780f;
    --badge-red: #9b2b26;
    --brand-slate: #7c8796;
  }
  html, body {
    margin: 0;
    padding: 0;
    width: 991px;
    height: 1200px;
    overflow: hidden;
    background: var(--backdrop);
  }
  .beer-label {
    position: absolute;
    left: 195px;
    top: 118px;
    width: 600px;
    height: 964px;
    display: block;
  }
  .label-top { fill: var(--label-white); }
  .label-bottom { fill: var(--label-dark); }
  .beer-name {
    font-family: "Cinzel", serif;
    font-weight: 700;
    font-size: 62px;
    letter-spacing: 2px;
    fill: var(--ink);
  }
  .helmet-art { fill: var(--helmet-grey); }
  .style-pale {
    font-family: "Jost", sans-serif;
    font-weight: 500;
    font-size: 138px;
    letter-spacing: -4px;
    fill: var(--pale-cream);
  }
  .style-ale {
    font-family: "Jost", sans-serif;
    font-weight: 600;
    font-size: 182px;
    letter-spacing: -6px;
    fill: var(--ale-amber);
  }
  .brand-badge { fill: var(--badge-red); }
  .brand-name {
    font-family: "Jost", sans-serif;
    font-weight: 500;
    font-size: 56px;
    letter-spacing: 4px;
    fill: var(--brand-slate);
  }
  .brand-tagline {
    font-family: "Jost", sans-serif;
    font-weight: 500;
    font-size: 22px;
    letter-spacing: 4px;
    fill: var(--brand-slate);
  }
</style>
</head>
<body>
<svg class="beer-label" viewBox="0 0 600 964" xmlns="http://www.w3.org/2000/svg" aria-label="Tidewren Pale Ale label, Meridian Tavern + Brewery">
  <defs>
    <path id="name-arc" d="M 240 232 A 190 150 0 0 1 560 232"/>
  </defs>

  <rect class="label-top" x="0" y="0" width="600" height="525"/>
  <rect class="label-bottom" x="0" y="525" width="600" height="439"/>

  <text class="beer-name" text-anchor="middle">
    <textPath href="#name-arc" startOffset="50%">TIDEWREN</textPath>
  </text>

  <rect class="helmet-art" x="250" y="200" width="300" height="250" rx="120" role="img" aria-label="Illustration of a crested Greek warrior helmet in profile"/>

  <text class="style-pale" x="26" y="530">PALE</text>
  <text class="style-ale" x="108" y="660">ALE</text>

  <circle class="brand-badge" cx="112" cy="877" r="58"/>
  <text class="brand-name" x="192" y="892">MERIDIAN</text>
  <text class="brand-tagline" x="196" y="930">TAVERN + BREWERY</text>
</svg>
</body>
</html>
```